Flat Belly Design Graphics for Social

I want to create 9 social media graphics (new Instagram size 4:5 (1080 x 1350 pixels) focusing on our Flat Belly Graphics, using the pics attached. Use the attached pics, NO RANDOM STOCK PHOTOGRAPHY. For the color scheme of the graphics, the color palette is attached. YOU MUST POST ALL 9 GRAPHICS IN ONE ENTRY.
Using the 3 titles below, create one set of graphics. 1) with all text, then for the others, use the pictures as detailed below in IMPORTANT:
1. Ten-Week Bright Morning Reboot
2. The Quick Garden Kitchen Menu Guide
3. Studio Habits for Lasting Energy Past Midlife - Zero Gym Needed
IMPORTANT:
Only use RK Pic 1 and RK Pic 2 with the title, Ten-Week Bright Morning Reboot
Only use meal plan1 and meal plan2 pics with the title, Quick Garden Kitchen Menu Guide
Only use studio habits 1 and studio habits 2 pics with the title, Studio Habits for Lasting Energy Past Midlife - Zero Gym Needed
women over 40

```html
<!DOCTYPE html>
<html lang="en">
<head>
<meta charset="UTF-8">
<title>Ten-Week Bright Morning Reboot</title>
<link href="https://fonts.googleapis.com/css2?family=Roboto:wght@400;700&display=swap" rel="stylesheet">
<style>
  :root {
    --rose: #E397AE;
    --blush: #F7DDE2;
    --forest: #2F4F4B;
    --white: #FFFFFF;
    --photo-light: #E9D9C6;
    --photo-mid: #B89372;
    --photo-dark: #5E4433;
  }
  html, body {
    margin: 0;
    padding: 0;
    width: 960px;
    height: 1200px;
    overflow: hidden;
    background: var(--rose);
  }
  .post {
    position: relative;
    width: 960px;
    height: 1200px;
    overflow: hidden;
    font-family: "Roboto", Arial, sans-serif;
  }
  .backdrop {
    position: absolute;
    inset: 0;
    width: 960px;
    height: 1200px;
  }
  .headline {
    position: absolute;
    top: 52px;
    left: 0;
    width: 960px;
    margin: 0;
    text-align: center;
    color: var(--white);
    font-weight: 400;
  }
  .headline-lead {
    display: block;
    font-weight: 700;
    font-size: 72px;
    line-height: 82px;
  }
  .headline-rest {
    display: block;
    font-size: 64px;
    line-height: 86px;
  }
</style>
</head>
<body>
<main class="post">
  <svg class="backdrop" viewBox="0 0 1080 1350" xmlns="http://www.w3.org/2000/svg">
    <defs>
      <clipPath id="lower-half"><rect x="0" y="865" width="1080" height="485"/></clipPath>
      <clipPath id="upper-half"><rect x="0" y="0" width="1080" height="865"/></clipPath>
      <linearGradient id="photo-tone" x1="0" y1="0" x2="0" y2="1">
        <stop offset="0" stop-color="var(--photo-dark)"/>
        <stop offset="0.45" stop-color="var(--photo-mid)"/>
        <stop offset="0.7" stop-color="var(--photo-light)"/>
        <stop offset="1" stop-color="var(--photo-dark)"/>
      </linearGradient>
    </defs>

    <rect class="sky" width="1080" height="1350" fill="var(--rose)"/>

    <g class="divider">
      <line x1="270" y1="287" x2="810" y2="287" stroke="var(--forest)" stroke-width="1.5"/>
      <rect x="440" y="281" width="202" height="12" rx="6" fill="var(--forest)"/>
    </g>

    <g class="base-panels" fill="var(--forest)">
      <path d="M0 585 C50 585 85 640 85 720 L85 1350 L0 1350 Z"/>
      <path d="M1080 585 C1030 585 1000 640 1000 720 L1000 1350 L1080 1350 Z"/>
      <rect x="0" y="865" width="1080" height="485"/>
    </g>

    <circle class="frame-lower" cx="544" cy="805" r="465" fill="var(--blush)" clip-path="url(#lower-half)"/>
    <circle class="frame-upper" cx="544" cy="805" r="440" fill="var(--forest)" clip-path="url(#upper-half)"/>

    <circle class="portrait" cx="544" cy="805" r="410" fill="url(#photo-tone)"
            role="img" aria-label="Photo of a smiling woman in a white cropped sweater pointing at her flat midsection in a modern kitchen"/>
  </svg>

  <h1 class="headline">
    <span class="headline-lead">Ten-Week</span>
    <span class="headline-rest">Bright Morning Reboot</span>
  </h1>
</main>
</body>
</html>
```